Business Card Design Project

Business Card
We are rebranding with a new logo
Industry/Entity Type
Business
Contact Information for Business Card
Dennis Morvale +61 487215963 dennis@quorv.com.au P.O. Box 872 Fernlow QLD 4309
Requirements
Must have
- Logo

```html
<!DOCTYPE html>
<html lang="en">
<head>
<meta charset="utf-8">
<title>Quorv International – Business Card</title>
<link rel="stylesheet" href="https://fonts.googleapis.com/css2?family=Roboto:wght@400;500;700&display=swap">
<style>
  :root {
    --backdrop: #262626;
    --card: #f3f3f3;
    --brand-blue: #1a8bc4;
    --blue-dark: #0b5a86;
    --blue-bright: #1f9fd8;
    --brand-orange: #ee8a1f;
    --text: #4a4a4a;
    --divider: #c9c9c9;
    --white: #ffffff;
  }
  * { box-sizing: border-box; margin: 0; padding: 0; }
  html, body {
    width: 1200px; height: 960px; overflow: hidden;
    background: var(--backdrop);
    font-family: "Roboto", Arial, sans-serif;
  }
  .card {
    position: absolute; left: 72px; top: 178px;
    width: 1056px; height: 604px;
    background: var(--card);
    overflow: hidden;
  }
  .brand {
    position: absolute; left: 60px; top: 238px; width: 440px;
    display: flex; align-items: center; justify-content: center; gap: 16px;
  }
  .brand-dot {
    width: 26px; height: 26px; border-radius: 50%;
    background: var(--brand-blue);
  }
  .brand-name {
    font-size: 44px; font-weight: 500; color: var(--brand-blue);
    white-space: nowrap;
  }
  .divider {
    position: absolute; left: 556px; top: 161px;
    width: 2px; height: 259px;
    background: linear-gradient(to bottom, transparent, var(--divider) 20%, var(--divider) 80%, transparent);
  }
  .contact { position: absolute; left: 612px; top: 178px; color: var(--text); }
  .contact-name {
    font-size: 34px; font-weight: 700; color: var(--brand-blue);
    letter-spacing: 0.5px; margin-bottom: 44px;
  }
  .contact-address { font-size: 25px; line-height: 32px; margin-bottom: 15px; }
  .contact-line {
    display: flex; align-items: center; gap: 14px;
    font-size: 25px; line-height: 33px;
  }
  .contact-line svg { width: 24px; height: 24px; flex: none; }
  .footer-art { position: absolute; left: 0; top: 0; }
  .website {
    position: absolute; left: 701px; top: 558px;
    font-size: 25px; color: var(--white); letter-spacing: 5px;
  }
</style>
</head>
<body>
  <div class="card">
    <div class="brand">
      <span class="brand-dot"></span>
      <span class="brand-name">Quorv International</span>
    </div>

    <div class="divider"></div>

    <div class="contact">
      <h1 class="contact-name">DENNIS MORVALE</h1>
      <p class="contact-address">P.O. Box 872<br>Fernlow QLD 4309</p>
      <p class="contact-line">
        <svg viewBox="0 0 24 24" aria-hidden="true"><path fill="#1a8bc4" d="M6.6 10.8c1.4 2.8 3.8 5.1 6.6 6.6l2.2-2.2c.3-.3.7-.4 1-.2 1.1.4 2.3.6 3.6.6.6 0 1 .4 1 1V20c0 .6-.4 1-1 1C10.6 21 3 13.4 3 4c0-.6.4-1 1-1h3.5c.6 0 1 .4 1 1 0 1.3.2 2.5.6 3.6.1.3 0 .7-.2 1z"/></svg>
        +61 487215963
      </p>
      <p class="contact-line">
        <svg viewBox="0 0 24 24" aria-hidden="true"><path fill="#1a8bc4" d="M3 5h18v14H3z"/><path fill="none" stroke="#f3f3f3" stroke-width="1.6" d="M3 6l9 7 9-7"/></svg>
        dennis@quorv.com.au
      </p>
    </div>

    <svg class="footer-art" width="1056" height="604" viewBox="0 0 1056 604" aria-hidden="true">
      <defs>
        <linearGradient id="web-band" x1="0" y1="0" x2="1" y2="0">
          <stop offset="0" stop-color="#0b5a86"/>
          <stop offset="0.6" stop-color="#1478ad"/>
          <stop offset="1" stop-color="#1f9fd8"/>
        </linearGradient>
      </defs>
      <rect x="0" y="568" width="600" height="36" fill="#ee8a1f"/>
      <path d="M584 604 Q604 540 690 536 L1056 536 L1056 604 Z" fill="url(#web-band)" stroke="#ffffff" stroke-width="4"/>
    </svg>
    <div class="website">www.quorv.com.au</div>
  </div>
</body>
</html>
```